Hi,
We are also sourcing for a logo, if you have ideas please take a look at our other project (if you look at our profile you should be able to see it).
We are looking for a website that will be used to manage mobile devices. The feature set is rather small, users can Wipe, Lock, Locate devices as well as make them Ring or Speak (by sending text to be spoken). We attached some images of what it looks like right now. We are looking for simplicity, uniformity and most importantly, the website should be thought of as primary User Interface, it should flow.
Please see attached to get an idea of what it looks like now. The current design was inspired by making a site that will work and flow well on a variety of displays (from mobile to tablet to desktop).
We want to stay away from radio buttons, check-boxes. This should be engaging and creative, opposite of Corporate. Not busy (ideally we are looking to have fewest possible choices at any given time and at the same time no feature should be more than 3 clicks away (this is a suggestion/approximation... just want to share our understanding of what 'flow' is).
Could be cartoony.
Thanks!
BrisketLoom
Reason: there are a couple of designs that are interesting, in addition to specific feedback I provided, possibly looking for more concepts.
Thank You

```html
<!DOCTYPE html>
<html lang="en">
<head>
<meta charset="utf-8">
<title>BrisketLoom — Find out what's happening</title>
<link rel="stylesheet" href="https://fonts.googleapis.com/css2?family=Mulish:wght@600;700;800&family=Arimo:wght@400&display=swap">
<style>
  :root {
    --ink: #222222;
    --ink-soft: #3a3a3a;
    --muted: #5e5e5e;
    --rule: #dedede;
    --frame: #c9c9c9;
    --pin: #8a8a8a;
    --bg: #ffffff;
    --badge: #0b0b0b;
  }
  * { box-sizing: border-box; margin: 0; padding: 0; }
  html, body { width: 1200px; height: 800px; overflow: hidden; background: var(--bg); }
  body { position: relative; font-family: "Arimo", Arial, sans-serif; color: var(--ink); }

  .site-header { position: absolute; left: 0; top: 0; width: 1200px; height: 108px; border-bottom: 1px solid var(--rule); }
  .brand { position: absolute; left: 135px; top: 36px; font-family: "Mulish", sans-serif; font-weight: 800; font-size: 37px; color: var(--ink-soft); letter-spacing: -0.3px; }
  .main-nav { position: absolute; right: 125px; top: 48px; font-family: "Mulish", sans-serif; font-weight: 700; font-size: 15px; color: var(--ink-soft); }
  .main-nav a { color: inherit; text-decoration: none; }
  .main-nav .sep { margin: 0 9px; font-weight: 400; }

  .hero-devices { position: absolute; left: 165px; top: 160px; width: 395px; height: 300px; border-radius: 30px; background: linear-gradient(180deg, #2b2b2b 0%, #3d6f9c 18%, #e9eef2 40%, #d8dde2 80%, #2b2b2b 100%); }
  .hero-shadow { position: absolute; left: 175px; top: 450px; width: 380px; height: 50px; border-radius: 50%; background: radial-gradient(ellipse at center, rgba(0,0,0,0.18) 0%, rgba(0,0,0,0) 70%); }

  .welcome-title { position: absolute; left: 130px; top: 512px; font-family: "Mulish", sans-serif; font-weight: 800; font-size: 37px; color: var(--ink-soft); letter-spacing: 0.5px; }
  .welcome-lead { position: absolute; left: 135px; top: 572px; width: 480px; font-family: "Mulish", sans-serif; font-weight: 800; font-size: 17.5px; line-height: 30px; color: var(--ink-soft); text-transform: uppercase; letter-spacing: 0.4px; }
  .store-badge { position: absolute; left: 242px; top: 659px; width: 159px; height: 54px; border-radius: 6px; background: var(--badge); border: 1px solid #9a9a9a; }

  .column-divider { position: absolute; left: 668px; top: 177px; width: 1px; height: 548px; background: var(--rule); }

  .feature-title { position: absolute; font-family: "Mulish", sans-serif; font-weight: 800; font-size: 24px; color: #111; }
  .feature-frame { position: absolute; width: 203px; height: 131px; border: 1px solid var(--frame); background: #fff; box-shadow: 0 1px 2px rgba(0,0,0,0.08); }
  .feature-photo { position: absolute; left: 10px; top: 10px; width: 181px; height: 110px; }
  .photo-lost { background: linear-gradient(90deg, #2f4a6b 0%, #3b5a80 45%, #b89a86 70%, #f2f2f2 100%); }
  .photo-protect { background: linear-gradient(90deg, #f4f4f4 0%, #5a5a5a 28%, #dcdcdc 55%, #e8e8e8 100%); }

  .feature-intro { position: absolute; font-size: 12.5px; color: var(--muted); }
  .feature-list { position: absolute; list-style: none; font-size: 12.5px; color: var(--muted); }
  .feature-list li { position: relative; height: 28px; padding-left: 14px; }
  .feature-list li svg { position: absolute; left: 0; top: 1px; }

  .section-divider { position: absolute; left: 717px; top: 415px; width: 336px; height: 1px; background: var(--rule); }

  .site-footer { position: absolute; left: 120px; top: 771px; width: 960px; border-top: 1px solid var(--rule); font-size: 12px; color: #444; }
  .site-footer .copyright { position: absolute; left: 0; top: 9px; }
  .site-footer .footer-links { position: absolute; right: -3px; top: 9px; }
  .footer-links a { color: inherit; text-decoration: none; }
</style>
</head>
<body>
  <header class="site-header">
    <div class="brand">BrisketLoom</div>
    <nav class="main-nav"><a href="#">Discover Apps</a><span class="sep">|</span><a href="#">Get Apps</a></nav>
  </header>

  <div class="hero-devices" role="img" aria-label="Three smartphones showing a social feed app"></div>
  <div class="hero-shadow"></div>

  <h1 class="welcome-title">WELCOME</h1>
  <p class="welcome-lead">Find out what’s happening, right now , with the mobile devices you care about.</p>
  <a class="store-badge" href="#" aria-label="App store badge"></a>

  <div class="column-divider"></div>

  <h2 class="feature-title" style="left:723px; top:130px;">Lost or Stolen Phone?</h2>
  <div class="feature-frame" style="left:724px; top:175px;">
    <div class="feature-photo photo-lost" role="img" aria-label="Hand taking a phone from a jeans back pocket"></div>
  </div>
  <p class="feature-intro" style="left:726px; top:321px;">Find your phone when you need it most by maps or ringer</p>
  <ul class="feature-list" style="left:724px; top:351px;">
    <li><svg width="8" height="12" viewBox="0 0 8 12"><path d="M4 0a4 4 0 0 1 4 4c0 3-4 8-4 8S0 7 0 4a4 4 0 0 1 4-4z" fill="var(--pin)"/></svg>Remotely wipe your confidential data</li>
    <li style="margin-top:2px;"><svg width="8" height="12" viewBox="0 0 8 12"><path d="M4 0a4 4 0 0 1 4 4c0 3-4 8-4 8S0 7 0 4a4 4 0 0 1 4-4z" fill="var(--pin)"/></svg>Register your stolen phone</li>
  </ul>

  <div class="section-divider"></div>

  <h2 class="feature-title" style="left:722px; top:429px;">Protect and Secure</h2>
  <div class="feature-frame" style="left:722px; top:473px;">
    <div class="feature-photo photo-protect" role="img" aria-label="Plush toy holding a phone beside a laptop"></div>
  </div>
  <ul class="feature-list" style="left:726px; top:618px;">
    <li><svg width="8" height="12" viewBox="0 0 8 12"><path d="M4 0a4 4 0 0 1 4 4c0 3-4 8-4 8S0 7 0 4a4 4 0 0 1 4-4z" fill="var(--pin)"/></svg>Monitor instant messaging like sms</li>
    <li><svg width="8" height="12" viewBox="0 0 8 12"><path d="M4 0a4 4 0 0 1 4 4c0 3-4 8-4 8S0 7 0 4a4 4 0 0 1 4-4z" fill="var(--pin)"/></svg>Record voice Commentaries</li>
    <li><svg width="8" height="12" viewBox="0 0 8 12"><path d="M4 0a4 4 0 0 1 4 4c0 3-4 8-4 8S0 7 0 4a4 4 0 0 1 4-4z" fill="var(--pin)"/></svg>Camera Observation</li>
    <li><svg width="8" height="12" viewBox="0 0 8 12"><path d="M4 0a4 4 0 0 1 4 4c0 3-4 8-4 8S0 7 0 4a4 4 0 0 1 4-4z" fill="var(--pin)"/></svg>Get notified if your child is skipping class</li>
    <li><svg width="8" height="12" viewBox="0 0 8 12"><path d="M4 0a4 4 0 0 1 4 4c0 3-4 8-4 8S0 7 0 4a4 4 0 0 1 4-4z" fill="var(--pin)"/></svg>Backup and share your pictures and contacts</li>
  </ul>

  <footer class="site-footer">
    <span class="copyright">© 2012 BrisketLoom INC,</span>
    <span class="footer-links"><a href="#">Terms &amp; Conditions</a> | <a href="#">Privacy Policy</a> | <a href="#">FAQs</a> | <a href="#">About</a> | <a href="#">Contact</a></span>
  </footer>
</body>
</html>
```